Road Construction Company needs business cards

We would like a new business card designed for our business.

We're a road construction company based in Qld, Australia.

Can the business card please have the following information on it.

Name: Warren Halbeck
Position: General Manager
Phone: 0472 915 348
Email: Warren.halbeck@tovrin.com.au
Address: 87 Marrow Ave, Pendlebay, QLD, 4023
Website: www.tovrin.com.au

Visually we'd like the card to be professional and simple.

Attached is our logo.

Our website is www.tovrin.com.au

Target Market(s)

Men aged 25-60

Contact Information for Business Card

As listed in project description

Font styles to use
Serif

Requirements
Must have
• Large logo on back of card

```html
<!DOCTYPE html>
<html lang="en">
<head>
<meta charset="utf-8">
<title>Tovrin Road Construction – Business Card</title>
<link rel="stylesheet" href="https://fonts.googleapis.com/css2?family=Poppins:wght@400;600;700&display=swap">
<style>
  :root {
    --backdrop: #2b2b2d;
    --card-white: #fbfbfb;
    --brand-blue: #1565c0;
    --brand-deep: #0d4fa8;
    --brand-sky: #2ea3dc;
    --ink: #333;
  }
  html, body {
    margin: 0;
    width: 1200px;
    height: 904px;
    overflow: hidden;
    background: var(--backdrop);
    font-family: "Poppins", sans-serif;
  }
  .stage { position: relative; width: 1200px; height: 904px; }
  .card {
    position: absolute;
    width: 520px;
    height: 317px;
    border-radius: 3px;
    overflow: hidden;
    box-shadow: 0 10px 24px rgba(0,0,0,.45);
  }
  .card-front { left: 110px; top: 100px; background: var(--card-white); }
  .card-back  { left: 570px; top: 487px; }

  .front-shapes { position: absolute; inset: 0; width: 100%; height: 100%; }

  .brand-name {
    position: absolute;
    left: 42px;
    top: 54px;
    margin: 0;
    font-size: 44px;
    font-weight: 700;
    letter-spacing: 1px;
    color: var(--brand-blue);
    line-height: 1;
  }
  .person { position: absolute; left: 42px; top: 138px; }
  .person-name {
    margin: 0;
    font-size: 24px;
    font-weight: 700;
    color: var(--brand-deep);
    line-height: 1.15;
  }
  .person-role {
    margin: 0;
    font-size: 15px;
    font-weight: 400;
    color: var(--brand-sky);
  }
  .divider {
    width: 22px; height: 3px;
    background: var(--brand-sky);
    margin: 10px 0 12px;
  }
  .contact { margin: 0; padding: 0; list-style: none; font-size: 11.5px; color: var(--ink); line-height: 1.55; }
  .contact li { display: flex; align-items: center; gap: 7px; }
  .contact .address { display: block; margin-bottom: 2px; }
  .contact svg { width: 11px; height: 11px; fill: var(--brand-deep); flex: none; }

  .back-field {
    position: absolute; inset: 0;
    background: radial-gradient(circle at 80% 20%, #2f78d0 0%, var(--brand-blue) 45%, #0f55b4 100%);
  }
  .back-logo {
    position: absolute;
    left: 0; right: 0; top: 50%;
    transform: translateY(-50%);
    margin: 0;
    text-align: center;
    font-size: 60px;
    font-weight: 700;
    letter-spacing: 2px;
    color: #fff;
  }
</style>
</head>
<body>
<main class="stage">
  <section class="card card-front" aria-label="Business card front">
    <svg class="front-shapes" viewBox="0 0 520 317" preserveAspectRatio="none" aria-hidden="true">
      <polygon points="447,0 520,0 520,317 437,128 447,128" fill="var(--brand-blue)"/>
      <polygon points="302,317 520,317 416,205" fill="var(--brand-sky)"/>
    </svg>

    <p class="brand-name">TOVRIN</p>

    <div class="person">
      <h1 class="person-name">Warren Halbeck</h1>
      <p class="person-role">General Manager</p>
      <div class="divider"></div>
      <ul class="contact">
        <li class="address">87 Marrow Ave,<br>Pendlebay, QLD, 4023</li>
        <li>
          <svg viewBox="0 0 24 24"><path d="M6.6 10.8a15 15 0 0 0 6.6 6.6l2.2-2.2c.3-.3.7-.4 1-.2 1.1.4 2.3.6 3.6.6.6 0 1 .4 1 1V20c0 .6-.4 1-1 1A17 17 0 0 1 3 4c0-.6.4-1 1-1h3.5c.6 0 1 .4 1 1 0 1.3.2 2.5.6 3.6.1.3 0 .7-.2 1z"/></svg>
          0472 915 348
        </li>
        <li>
          <svg viewBox="0 0 24 24"><path d="M2 5h20v14H2zm2 2v.5l8 5 8-5V7l-8 5z"/></svg>
          Warren.halbeck@tovrin.com.au
        </li>
        <li>
          <svg viewBox="0 0 24 24"><path d="M12 2a10 10 0 1 0 0 20 10 10 0 0 0 0-20zm6.9 6h-3a15 15 0 0 0-1.3-3.9A8 8 0 0 1 18.9 8zM12 4c.8 1.2 1.5 2.5 1.9 4h-3.8c.4-1.5 1.1-2.8 1.9-4zM4.3 14a8 8 0 0 1 0-4h3.4a16 16 0 0 0 0 4zm.8 2h3a15 15 0 0 0 1.3 3.9A8 8 0 0 1 5.1 16zm3-8h-3a8 8 0 0 1 4.3-3.9C8.8 5.3 8.4 6.6 8.1 8zM12 20c-.8-1.2-1.5-2.5-1.9-4h3.8c-.4 1.5-1.1 2.8-1.9 4zm2.3-6H9.7a14 14 0 0 1 0-4h4.6a14 14 0 0 1 0 4zm.3 5.9c.6-1.2 1-2.5 1.3-3.9h3a8 8 0 0 1-4.3 3.9zm1.7-5.9a16 16 0 0 0 0-4h3.4a8 8 0 0 1 0 4z"/></svg>
          www.tovrin.com.au
        </li>
      </ul>
    </div>
  </section>

  <section class="card card-back" aria-label="Business card back">
    <div class="back-field" role="img" aria-label="Blue background with a faint repeating brand pattern"></div>
    <p class="back-logo">TOVRIN</p>
  </section>
</main>
</body>
</html>
```